Business Card Design - Amberfield Court

We are looking at a new design for our business cards that has a modern and professional look. We run a residential aged care facility focussing on the care of residents. The cards will be used for potential clients, consultants and business opportunities in this sector. Blue and white is our main colours and would to see these colours incorporated in the design.
Industry/Entity Type
Business
Contact Information for Business Card
Amberfield Court, Darren Walsh, dwalsh@amberfieldcourt.com.au, Finance Manager, 0472 639 208, BCom, 37 Marrabel Crescent, Brindle Vale, Qld 4093.
Look and feel
Each slider illustrates characteristics of the customer's brand and the style your logo design should communicate.

```html
<!DOCTYPE html>
<html lang="en">
<head>
<meta charset="utf-8">
<title>Amberfield Court – Business Card</title>
<link href="https://fonts.googleapis.com/css2?family=Open+Sans:wght@400;600;700;800&display=swap" rel="stylesheet">
<style>
  :root {
    --stage: #2b2b2d;
    --teal: #1c3a4a;
    --taupe: #b3a89d;
    --white: #ffffff;
  }
  html, body {
    margin: 0;
    padding: 0;
    width: 1200px;
    height: 900px;
    overflow: hidden;
    background: var(--stage);
    font-family: "Open Sans", Arial, sans-serif;
  }
  .canvas {
    position: relative;
    width: 1200px;
    height: 900px;
  }
  .card {
    position: absolute;
    left: 280px;
    width: 640px;
    height: 366px;
    border-radius: 22px;
    overflow: hidden;
  }
  .card-back { top: 44px; background: var(--white); }
  .card-front { top: 490px; background: var(--taupe); }

  .card-back svg, .card-front svg.shapes {
    position: absolute;
    inset: 0;
  }
  .back-name {
    position: absolute;
    left: 0;
    right: 0;
    top: 250px;
    text-align: center;
    color: var(--white);
    font-weight: 700;
    font-size: 40px;
    letter-spacing: 1px;
  }

  .front-brand {
    position: absolute;
    left: 30px;
    top: 110px;
    display: flex;
    align-items: center;
    gap: 12px;
  }
  .front-brand .mark {
    width: 34px;
    height: 34px;
    border-radius: 50%;
    background: var(--teal);
  }
  .front-brand .name {
    color: var(--teal);
    font-weight: 700;
    font-size: 24px;
    letter-spacing: 0.5px;
  }

  .contact {
    position: absolute;
    left: 392px;
    top: 112px;
    color: var(--white);
  }
  .contact .person {
    margin: 0;
    font-weight: 800;
    font-size: 25px;
    line-height: 1.1;
    text-transform: uppercase;
  }
  .contact .role {
    margin: 2px 0 12px;
    font-size: 12.5px;
    text-transform: uppercase;
  }
  .contact p {
    margin: 0;
    font-size: 13.5px;
    line-height: 1.45;
  }
  .contact .address { margin-bottom: 8px; }
  .contact .line {
    display: flex;
    align-items: center;
    gap: 6px;
  }
  .contact .line svg { flex: none; }
</style>
</head>
<body>
<div class="canvas">

  <section class="card card-back" aria-label="Business card back">
    <svg width="640" height="366" viewBox="0 0 640 366">
      <circle cx="320" cy="380" r="230" fill="var(--teal)"/>
    </svg>
    <div class="back-name">Amberfield Court</div>
  </section>

  <section class="card card-front" aria-label="Business card front">
    <svg class="shapes" width="640" height="366" viewBox="0 0 640 366">
      <path d="M230 0 C330 20 320 200 350 280 C370 335 420 366 460 366 L640 366 L640 0 Z" fill="var(--teal)"/>
      <path d="M230 0 C330 20 320 200 350 280 C370 335 420 366 460 366" fill="none" stroke="var(--white)" stroke-width="6"/>
    </svg>

    <div class="front-brand">
      <span class="mark"></span>
      <span class="name">Amberfield Court</span>
    </div>

    <div class="contact">
      <h1 class="person">Darren Walsh</h1>
      <div class="role">Finance Manager (BCom)</div>
      <div class="address">
        <p>37 Marrabel Crescent</p>
        <p>Brindle Vale, Qld 4093</p>
      </div>
      <p class="line">
        <svg width="12" height="12" viewBox="0 0 24 24" aria-hidden="true"><path fill="#fff" d="M6.6 10.8a15.1 15.1 0 0 0 6.6 6.6l2.2-2.2c.3-.3.7-.4 1-.2 1.1.4 2.3.6 3.6.6.6 0 1 .4 1 1V20c0 .6-.4 1-1 1A17 17 0 0 1 3 4c0-.6.4-1 1-1h3.5c.6 0 1 .4 1 1 0 1.3.2 2.5.6 3.6.1.3 0 .7-.2 1z"/></svg>
        0472 639 208
      </p>
      <p class="line">
        <svg width="12" height="10" viewBox="0 0 24 18" aria-hidden="true"><rect x="1" y="1" width="22" height="16" rx="2" fill="none" stroke="#fff" stroke-width="2"/><path d="M1 2 L12 10 L23 2" fill="none" stroke="#fff" stroke-width="2"/></svg>
        dwalsh@amberfieldcourt.com.au
      </p>
    </div>
  </section>

</div>
</body>
</html>
```